Nutritional & Gastrointestinal Health Consulting Service-Website design

We need a website design for a new health consulting service called "Bright Vale" based in Perth, Australia.

We will be providing consulting services in the areas of:
1) Nutrition and Diet
2) Gastrointestinal Health (which means stomach & digestive system related health)

These consulting services will be provided by an Accredited Dietitian and a Paediatric Gastroenterologist.

We are open to creative ideas in terms of design, layout, fonts and colours. We also would love to see images of nature in the backdrop with families (adults with kids) having a good time, fresh fruits and vegetables displayed in a farmer's market or supermarket. 2 or 3 images should be sufficient. We would also definitely want our logo somewhere in the main page of website. The logo file is also attached. Please have a look at a website's design that we really liked. We would love to see designs inspired by that style. The website details are in the in the "nice to have priorities" section of this project brief.

We also would be looking at website designers with software coding skills so that if we like the design we can go ahead with the next step of coding.

The website design should communicate the purpose of the website and at the same time be simple, elegant and unique/eye-catching.

We look forward to receiving creative ideas for our website from you all. Good luck!

More details have been added to our project- for example: Logo, fonts style, must haves etc etc. Please view the updated project brief. Looking forward to receiving your fantastic ideas for our website. Thanking you

Hi, I have updated the colour preference. Will add the content preferences tomorrow. thanks

Hello all, I have now added a LOT more content to what we want in our website. It is very much in detail, so please carefully have a read through the entire project brief. If you have any questions write back to me and I will try to respond as quickly as I can. Last few days were busy so couldn't respond quickly to all of you who had send me designs/queries/questions. Thank you for your patience. I look forward to receiving fantastic designs from you all. Good Luck :-)

Target Market(s)

Adults based in western speaking countries aged 18 to 60 years

Industry/Entity Type

Software

Font styles to use
Sans Serif
Script

Colors
faa54b
acd036

Requirements
Must have
• The website must have the MAIN logo file attached. I have attached 3 files: 1) MAIN logo; 2) supplementary logo A ; 3) supplementary logo B

I have selected 2 colours from the colour scheme (see below)-(as the colour of our logo is that).
However we would also like to see LIGHT CHOCOLATE BROWN or CHOCOLATE BROWN colour used as the background colour of the website
Preferred WEBSITE CONTENT:
1) HOME PAGE:
Content required=
--Company Logo
--Dr Dorian Pelham
Paediatric Gastroenterologist & Hepatologist
-Marla Pelham.
Dietitian & Nutritionist
--Website Menu (either listed horizontally or vertically):
Once clicked on each name:

Under each of the Website Menu items we want the following Headings to be added

2) ABOUT US page:
Sub-heading under this: Qualification, Skills, Special Interest

3) SERVICES
DORIAN'S PAGE: Individual Consultation, Endoscopy procedures
Individual Consultation, Group Based Services, Food Diary, Food & Symptom Diary

4) FEES & REBATE: Content as below:
Please Note: Payment of full fees is required at the time of consultation and procedures. 48 hours notice is required for cancellation of appointments/non-attendance. Failure to provide this may result in a fee being incurred. Please call reception to find out the amount of fee charged for cancellation of appointments/non-attendance.
headings are:
Paediatric Gastroenterology:
Dorian's pge
Individual Consultation - Initial (upto 30 mins):
Review Consultation (upto 15 mins):
Endoscopy procedures - No Gap fees charged. Fees will be billed directly to Vitacover. If any queries, please contact reception.

marla's pge
sub heading:
Individual Consultation - Initial (upto 45 mins):
Individual Consultation - Review (upto 30 mins):

Concession-Individual Consultation -Initial (upto 45 mins):
Concession-Individual Consultation - Review (upto 30 mins):
Please Note: Concession applies for health care card holders & pensioners

Group Based Services: Pricing subject to the type of service provided. Please contact us for an obligation free quote.
Education Topics Include:
- Paediatric Nutrition (Introducing Solids, Fussy Eating, Healthy Eating)
- Pregnancy Nutrition, Gestational Diabetes, Breastfeeding/Lactation Nutrition
- Healthy Eating, Supermarket Shopping Tips, Nutrition Label Reading Tips, Healthier
sub heading under nutrition & diet:
-Vitacover:
--A rebate of $52.95 is available from Vitacover if an EPC ( Enhanced Primary Care)/Chronic Disease Management (CDM) plan is issued by your GP.
--All mandatory paperwork needs to be available at the time of making your appointment for your eligibility.
-Private Health Fund:
--Most private health funds provide rebate on dietetic appointments. However the rebate amount depends on your level of cover. Thus, please contact your health fund to determine your entitled rebate.
-RSB: Approved provider for RSB services

6) FOR DOCTORS: Bright Vale Paediatric Gastroenterologist Referral Form
Bright Vale Dietitian Referral form
7) LOCATIONS & CONTACT

Paediatric Gastroenterology & Hepatology Service
Suite 46
Holy Lantern Bramcote Medical Centre
17 Colin Ferris Pde,
MURDOCH, WA 6150
P: (08) 9422 5061
F: (08) 9422 3094

Nutrition & Diet Service
Suite 46
17 Colin Ferris Pde,
MURDOCH, WA 6150
P: (08) 9422 5061
F: (08) 9422 3094

Tolland Medical Centre
58-60 Karrigan Parkway,
MANDURAH, WA 6210
P: (08) 9647 2283
F: (08) 96724419
www.tmcexample.com.au

This page should have a webform that has following titles:
-Your Name
-Your Email
-Your Phone
-Message

8) NEWS & BLOG
Nice to have
• We liked the design style of the websites below:
https://www.vendoraplex.example/

http://qoravelt.example/

But feel free to use your creativity too
Should not have
• Please do not use any body building or muscle building images

```html
<!DOCTYPE html>
<html lang="en">
<head>
<meta charset="utf-8">
<title>Bright Vale – Contact</title>
<link href="https://fonts.googleapis.com/css2?family=Arimo:wght@400;700&display=swap" rel="stylesheet">
<style>
  :root {
    --page-brown: #5b3419;
    --frame-fill: #b3a193;
    --frame-line: #f4f0ec;
    --panel-brown: #7d5f4b;
    --content-fill: #d3c7bf;
    --heading-brown: #5a2f14;
    --link-orange: #faa54b;
    --link-green: #d4ea5c;
    --text-dark: #111;
    --text-light: #fff;
    --required: #c0271d;
    --field-line: #b8b0aa;
  }
  * { box-sizing: border-box; margin: 0; padding: 0; }
  html, body { width: 1200px; height: 882px; overflow: hidden; }
  body { position: relative; font-family: "Arimo", Arial, sans-serif; color: var(--text-dark); }

  .backdrop { position: absolute; inset: 0; background: var(--page-brown); }
  .page-frame {
    position: absolute; left: 35px; top: 37px; width: 1130px; height: 808px;
    background: var(--frame-fill); border: 3px solid var(--frame-line); border-radius: 14px;
  }
  .account-links { position: absolute; right: 42px; top: 6px; font-size: 13px; color: #e8ddd5; }
  .account-links a { color: #5a3a22; }
  .account-links .divider { margin: 0 8px; }

  .site-header {
    position: absolute; left: 212px; top: 22px; width: 698px; height: 177px;
    background: var(--panel-brown); border: 3px solid var(--frame-line); border-radius: 16px;
    display: flex; align-items: center; justify-content: center;
  }
  .brand-name { font-size: 30px; font-weight: 700; color: var(--text-light); }

  .side-panel {
    position: absolute; background: var(--panel-brown);
    border: 3px solid var(--frame-line); border-radius: 6px; color: var(--text-light);
  }
  .panel-title {
    text-align: center; font-size: 15px; font-weight: 700; padding: 4px 0 5px;
    border-bottom: 3px solid #c9bcb2;
  }
  .main-menu { left: 24px; top: 218px; width: 224px; height: 242px; }
  .main-menu ul { list-style: circle; padding: 20px 0 0 56px; color: #222; }
  .main-menu li { font-size: 13px; font-weight: 700; line-height: 15px; margin-bottom: 2.6px; }
  .main-menu a { color: var(--link-orange); }
  .main-menu a.is-featured { color: var(--link-green); }

  .user-login { left: 877px; top: 218px; width: 224px; height: 212px; }
  .user-login form { padding: 17px 14px 0 14px; font-size: 13px; }
  .user-login label { display: block; font-weight: 700; margin-bottom: 1px; }
  .user-login .field { width: 108px; height: 20px; border: 1px solid #999; background: #fff;
    font-size: 13px; padding: 1px 3px; margin-bottom: 13px; font-family: inherit; }
  .user-login ul { padding-left: 20px; list-style: disc; margin-top: 2px; }
  .user-login ul a { color: var(--link-green); }
  .req { color: var(--required); }
  .button { font-family: inherit; font-size: 12px; padding: 2px 9px; border: 1px solid #888;
    background: linear-gradient(#fafafa, #ddd); border-radius: 2px; color: #111; }
  .user-login .button { margin-top: 13px; }

  .content-panel {
    position: absolute; left: 258px; top: 218px; width: 608px; height: 524px;
    background: var(--content-fill); border: 3px solid var(--frame-line); border-radius: 6px;
    padding: 3px 10px 0 10px;
  }
  .breadcrumb { font-size: 13px; font-weight: 700; padding: 1px 0 3px 10px; border-bottom: 3px solid #a89c94; }
  .breadcrumb a { color: var(--text-dark); }
  .page-title { font-size: 20px; color: var(--heading-brown); margin: 9px 0 0; }
  .byline { font-size: 10px; margin: 38px 0 0 14px; }
  .contact-form { padding: 23px 0 0 13px; }
  .contact-form label { display: block; font-size: 13px; font-weight: 700; margin-bottom: 1px; }
  .contact-form .field { display: block; width: 350px; height: 20px; border: 1px solid var(--field-line);
    background: #fff; margin-bottom: 12px; }
  .contact-form textarea.field { width: 557px; height: 92px; resize: none; margin-bottom: 14px; }
  .content-rule { position: absolute; left: 23px; right: 23px; bottom: 20px; border-top: 3px solid #a89c94; }

  .site-footer { position: absolute; left: 0; right: 0; top: 764px; text-align: center;
    font-size: 13px; font-weight: 700; color: var(--text-dark); }
  .site-footer a { color: var(--text-dark); }
</style>
</head>
<body>
  <div class="backdrop" role="img" aria-label="Sketched fruit and vegetable pattern on chocolate brown"></div>

  <div class="page-frame">
    <nav class="account-links"><a href="#">Login</a><span class="divider">|</span><a href="#">Register</a></nav>

    <header class="site-header">
      <span class="brand-name">Bright Vale</span>
    </header>

    <aside class="side-panel main-menu">
      <h2 class="panel-title">Main menu</h2>
      <ul>
        <li><a href="#">Home</a></li>
        <li><a href="#">About Us</a></li>
        <li><a href="#">Nutrition &amp; Diet</a></li>
        <li><a href="#">Paediatric Gastroenterology</a></li>
        <li><a href="#">Fees &amp; Rebate</a></li>
        <li><a href="#">For Doctors</a></li>
        <li><a href="#">Location</a></li>
        <li><a href="#">Contact</a></li>
        <li><a href="#" class="is-featured">News &amp; Blog</a></li>
      </ul>
    </aside>

    <main class="content-panel">
      <div class="breadcrumb"><a href="#">Home</a></div>
      <h1 class="page-title">Contact</h1>
      <p class="byline">published by Tamsin on Sat, 10/25/2014 - 03:07</p>
      <form class="contact-form">
        <label>Name <span class="req">*</span></label><input class="field" type="text">
        <label>Email <span class="req">*</span></label><input class="field" type="text">
        <label>Telephone <span class="req">*</span></label><input class="field" type="text">
        <label>Subject <span class="req">*</span></label><input class="field" type="text">
        <label>Message <span class="req">*</span></label><textarea class="field"></textarea>
        <button class="button" type="button">Submit</button>
      </form>
      <div class="content-rule"></div>
    </main>

    <aside class="side-panel user-login">
      <h2 class="panel-title">User login</h2>
      <form>
        <label>Username <span class="req">*</span></label>
        <input class="field" type="text" value="Tamsin">
        <label>Password <span class="req">*</span></label>
        <input class="field" type="password" value="xxxxxxxxxxx">
        <ul><li><a href="#">Request new password</a></li></ul>
        <button class="button" type="button">Log in</button>
      </form>
    </aside>

    <footer class="site-footer"><a href="#">Bright Vale</a> © Copyright 2014</footer>
  </div>
</body>
</html>
```